Upland Bird Hunting Preserve and Pointing Dog kennel

Need Price packages outlined for the bird hunting business. List the kennel and that we provide training and dogs for sale.
The preserve is "Tall Heron Provisions" the dog kennel is "Pine Hollow Setters"
1/2 Day Upland Field Hunts: 5 Pheasants $120
7 Chukar $125
Continental Hunt 12 Pheasants $325 includes meal, minimum 12 hunters
Guides available $100

Target Market(s)

upland bird hunters

Industry/Entity Type

hunting, outdoor

Colors
EE7325
F08F49
F5BC92
FAE3D3
FDF4ED

```html
<!DOCTYPE html>
<html lang="en">
<head>
<meta charset="utf-8">
<title>Tall Heron Provisions – Hunting Packages</title>
<link href="https://fonts.googleapis.com/css2?family=Roboto:wght@300;400;500;700;900&display=swap" rel="stylesheet">
<style>
  :root {
    --orange: #EE7325;
    --orange-mid: #F08F49;
    --orange-soft: #F5BC92;
    --cream: #FAE3D3;
    --paper: #FDF4ED;
    --ink: #0b0b0b;
    --white: #ffffff;
  }
  * { box-sizing: border-box; margin: 0; padding: 0; }
  html, body { width: 954px; height: 1200px; overflow: hidden; }
  body { font-family: "Roboto", Arial, sans-serif; background: var(--orange); color: var(--white); }
  .flyer { position: relative; width: 954px; height: 1200px; background: var(--orange); overflow: hidden; }

  .header { position: absolute; left: 0; top: 0; width: 954px; height: 155px; background: var(--white); color: var(--ink); }
  .brand-name { position: absolute; left: 67px; top: 34px; font-size: 36px; font-weight: 700; letter-spacing: 0.2px; white-space: nowrap; }
  .brand-town { position: absolute; left: 67px; top: 78px; width: 551px; display: flex; align-items: center; gap: 18px; }
  .brand-town .rule { flex: 1; height: 2px; background: var(--orange); }
  .brand-town span { font-size: 28px; font-weight: 700; letter-spacing: 3.5px; }
  .brand-tag { position: absolute; left: 67px; top: 116px; font-size: 18px; font-weight: 700; letter-spacing: 10.2px; white-space: nowrap; }

  .kennel { position: absolute; left: 700px; top: 48px; width: 190px; text-align: center; color: var(--ink); }
  .kennel-name { display: flex; align-items: center; justify-content: center; gap: 8px; font-size: 17px; font-weight: 700; letter-spacing: 0.5px; }
  .kennel-name .dot { width: 10px; height: 10px; border-radius: 50%; background: var(--ink); }
  .kennel-rule { margin: 40px auto 6px; width: 150px; height: 3px; background: var(--ink); }
  .kennel-town { font-size: 15px; font-weight: 500; letter-spacing: 0.5px; }

  .band { position: absolute; left: 0; width: 954px; background: var(--ink); }
  .band.top { top: 155px; height: 7px; }
  .band.bottom { top: 435px; height: 8px; }
  .hero-photo { position: absolute; left: 0; top: 162px; width: 954px; height: 273px;
    background: linear-gradient(180deg, #a89578 0%, #8b7458 45%, #6d5a48 70%, #b9ab9a 100%); }

  .section-tab { position: absolute; left: 0; top: 456px; width: 457px; height: 42px; background: var(--ink);
    clip-path: polygon(0 0, 97% 0, 100% 100%, 0 100%); }
  .section-tab h2 { position: absolute; left: 79px; top: 4px; font-size: 30px; font-weight: 700; letter-spacing: 0.3px; }

  .packages { position: absolute; left: 79px; top: 509px; width: 520px; }
  .package h3 { font-size: 25px; font-weight: 700; line-height: 30px; }
  .package p { font-size: 25px; font-weight: 300; line-height: 32px; }
  .package + .package { margin-top: 8px; }
  .divider { width: 320px; height: 1px; margin: 6px 0 12px; background: linear-gradient(90deg, var(--cream), rgba(250,227,211,0)); }

  .dog-photo { position: absolute; left: 603px; top: 491px; width: 300px; height: 296px; border-radius: 50%;
    border: 4px solid var(--white); box-shadow: 4px 6px 12px rgba(0,0,0,0.25);
    background: radial-gradient(circle at 50% 55%, #3a3836 0%, #5b4f3f 45%, #b08a4a 75%, #caa262 100%); }

  .field-photo { position: absolute; top: 815px; width: 381px; height: 201px; border-radius: 12px;
    border: 5px solid var(--white); box-shadow: 4px 6px 12px rgba(0,0,0,0.25); }
  .field-photo.left { left: 87px; background: linear-gradient(180deg, #8d7a63 0%, #6e5e4d 55%, #a9a19a 100%); }
  .field-photo.right { left: 486px; background: linear-gradient(180deg, #a3927a 0%, #c9a25a 50%, #5e6b7e 100%); }

  .services { position: absolute; left: 0; top: 1030px; width: 954px; text-align: center; }
  .services .lead { font-size: 27px; font-weight: 700; letter-spacing: 0.4px; }
  .services .sale { margin-top: 2px; font-size: 27px; font-weight: 400; letter-spacing: 0.4px; }
  .services .sale strong { font-weight: 700; }

  .contact { position: absolute; left: 257px; top: 1108px; width: 440px; }
  .contact-label { display: flex; align-items: center; gap: 10px; font-size: 18px; font-weight: 500; letter-spacing: 2.5px; position: relative; z-index: 1; }
  .contact-label .rule { flex: 1; height: 2px; background: var(--white); }
  .contact-label .rule.l { margin-left: 60px; }
  .contact-label .rule.r { margin-right: 60px; }
  .contact-pill { margin-top: -10px; height: 50px; border: 2px solid var(--white); border-top-color: transparent; border-radius: 26px;
    display: flex; align-items: center; justify-content: center; font-size: 24px; font-weight: 700; letter-spacing: 1px; }
</style>
</head>
<body>
<main class="flyer">
  <header class="header">
    <h1 class="brand-name">TALL HERON PROVISIONS, LLC</h1>
    <div class="brand-town"><i class="rule"></i><span>Alder Falls, MO</span><i class="rule"></i></div>
    <p class="brand-tag">LICENSED SHOOTING PRESERVE</p>
    <div class="kennel">
      <div class="kennel-name"><i class="dot"></i>PINE HOLLOW SETTERS</div>
      <div class="kennel-rule"></div>
      <div class="kennel-town">BIRCH FORD, MO</div>
    </div>
  </header>

  <div class="band top"></div>
  <div class="hero-photo" role="img" aria-label="Group of hunters standing behind a long row of harvested pheasants laid on a fallen log in winter woods"></div>
  <div class="band bottom"></div>

  <div class="section-tab"><h2>HUNTING PACKAGES</h2></div>

  <section class="packages">
    <div class="package">
      <h3>½ DAY UPLAND FIELD HUNTS</h3>
      <p>5 Pheasants — $120</p>
      <p>7 Chukar - $125</p>
    </div>
    <div class="divider"></div>
    <div class="package">
      <h3>CONTINENTAL PHEASANT HUNT</h3>
      <p>12 Pheasants — $325 (includes meal)</p>
      <p>12 Hunter Minimum</p>
    </div>
    <div class="divider"></div>
    <div class="package">
      <h3>GUIDES AVAILABLE</h3>
      <p>$100 per half day</p>
    </div>
  </section>

  <div class="dog-photo" role="img" aria-label="Ticked black pointing dog with orange collar standing in dry corn stalks"></div>

  <div class="field-photo left" role="img" aria-label="Two hunters and a pointing dog with a row of harvested chukar on a log"></div>
  <div class="field-photo right" role="img" aria-label="Hunters in blaze orange with a white dog and birds on a truck tailgate"></div>

  <section class="services">
    <p class="lead">Professional Dog Training available</p>
    <p class="sale">Puppies and Started Dogs <strong>for sale!</strong></p>
  </section>

  <section class="contact">
    <div class="contact-label"><i class="rule l"></i>CONTACT:<i class="rule r"></i></div>
    <div class="contact-pill">DALE MORROW : 555-014-2870</div>
  </section>
</main>
</body>
</html>
```